All-Natural Head Lice Removal company

I need a business card with my pre-existing logo. We are a new company located in Portland Oregon that goes into peoples homes to help with head lice removal. My products and approach are all- natural and also will be around children.On my current logo we used Teal Bl and the color Green. I am open to new ideas just want it simple and creative

Target Market(s)

my biggest market is families of school aged children

Industry/Entity Type

Business

Contact Information for Business Card

see upload for details from previous business card

Font styles to use
Serif

Colors
33a6d7
9bcb3b
f37122

Requirements
Must have
• Basic information/ logo put into a creative format that is catching to the eye
Nice to have
• creative

```html
<!DOCTYPE html>
<html lang="en">
<head>
<meta charset="utf-8">
<title>Nit Clear — Business Card</title>
<link href="https://fonts.googleapis.com/css2?family=Amaranth:wght@400;700&family=Open+Sans:wght@400;600&display=swap" rel="stylesheet">
<style>
  :root {
    --page: #ece9e4;
    --card-white: #f7f7f7;
    --green: #7dc142;
    --green-dark: #6cae35;
    --blue: #3ab0dc;
    --ink: #2f2f2f;
    --ink-soft: #4a4a4a;
    --white: #ffffff;
  }
  * { margin: 0; padding: 0; box-sizing: border-box; }
  html, body { width: 1200px; height: 1023px; overflow: hidden; }
  body {
    background: var(--page);
    position: relative;
    font-family: "Open Sans", sans-serif;
    color: var(--ink);
  }
  .card {
    position: absolute;
    width: 580px;
    height: 332px;
    border-radius: 26px;
    overflow: hidden;
    box-shadow: 0 10px 28px rgba(0,0,0,0.18);
  }

  /* Front */
  .card--front { left: 70px; top: 110px; background: var(--card-white); }
  .front__accent {
    position: absolute; right: 0; top: 0;
    width: 84px; height: 158px;
    background: var(--blue);
  }
  .front__band {
    position: absolute; left: 0; right: 0; top: 158px;
    height: 72px;
    background: var(--green);
  }
  .front__headline {
    position: absolute; left: 36px; top: 44px; width: 280px;
    font-family: "Amaranth", sans-serif; font-weight: 700;
    font-size: 26px; line-height: 1.2; color: var(--ink-soft);
  }
  .front__person {
    position: absolute; left: 40px; top: 170px;
    color: var(--white); font-family: "Amaranth", sans-serif;
  }
  .front__name { font-size: 25px; font-weight: 700; line-height: 1.1; }
  .front__role { font-size: 14px; font-weight: 700; margin-top: 2px; padding-left: 28px; }
  .brand {
    display: flex; flex-direction: column; align-items: center; gap: 6px;
  }
  .front__brand {
    position: absolute; right: 100px; top: 36px; width: 150px;
  }
  .brand__dot {
    width: 32px; height: 32px; border-radius: 50%;
    background: var(--green);
  }
  .brand__name {
    font-family: "Amaranth", sans-serif; font-weight: 700;
    font-size: 30px; color: var(--ink); line-height: 1; white-space: nowrap;
  }
  .front__contact {
    position: absolute; left: 120px; top: 246px;
    list-style: none; font-size: 14px; line-height: 1.5; color: var(--ink);
  }
  .front__contact b { color: var(--green); font-weight: 600; margin-right: 4px; }
  .front__contact .web-accent { color: var(--green-dark); }

  /* Back */
  .card--back { left: 560px; top: 600px; background: var(--green); }
  .back__brand {
    position: absolute; left: 0; right: 0; top: 48px;
  }
  .back__brand .brand__dot {
    width: 40px; height: 40px; background: transparent; border: 3px solid var(--ink);
  }
  .back__brand .brand__name { font-size: 40px; }
  .back__tagline {
    position: absolute; left: 40px; right: 40px; bottom: 40px;
    font-size: 16px; line-height: 1.5; color: var(--ink);
  }
  .back__tagline .web-accent { color: var(--blue); }
</style>
</head>
<body>
  <section class="card card--front" aria-label="Business card front">
    <div class="front__accent"></div>
    <div class="front__band"></div>
    <h1 class="front__headline">All Natural In-Home Lice Removal Services</h1>
    <div class="brand front__brand">
      <span class="brand__dot"></span>
      <span class="brand__name">Nit Clear</span>
    </div>
    <div class="front__person">
      <p class="front__name">Maren Holt</p>
      <p class="front__role">Owner</p>
    </div>
    <ul class="front__contact">
      <li><b>P :</b>1-555-014-NITS (6487)</li>
      <li><b>E :</b>maren@nitclear.com</li>
      <li><b>W :</b>www.<span class="web-accent">nitclear</span>.com</li>
    </ul>
  </section>

  <section class="card card--back" aria-label="Business card back">
    <div class="brand back__brand">
      <span class="brand__dot"></span>
      <span class="brand__name">Nit Clear</span>
    </div>
    <p class="back__tagline">
      Try Nit Clear Today and Be Lice Free Tomorrow!<br>
      All Natural In-Home Lice Removal Servise<br>
      www.<span class="web-accent">nitclear</span>.com
    </p>
  </section>
</body>
</html>
```